Sustainably Transforming Education

Company is education services based. early learning through adult and corporate. Focus is national government policy and program design and delivery alongside a research based and academically grounded set of approaches to planning, evaluation, and change management.I am looking for an innovative design position that aligns with the global agendas for innovation, creativity and collaboration at international and national policy levels (berulo is a name that reflects these qualities - colours need to reflect amythyst in some way). I also need a design that translates from a business card as 1 medium of interaction to a template that can work in word/powerpoint etc to support both stationery as well as a digital strategy across multiple channels (fb/twit/etc)There is no slogan/tag line for the company and their is no logo. I was looking to just leverage the name - have currently played around with various fonts (ending up with cuisine - all lowercase).

Industry/Entity Type

Adult

Contact Information for Business Card

name: berulo (all lowercase)Chairman: Andrew CrowMobile: +61 418 902 131Web: www.berulo.comemail: martin.pelly@berulo-example.com

Font styles to use
Script
Other font styles liked:
• cuisine

Colors
e34298
e667a6
33a6d7
aaaaaa

Requirements
Nice to have
• https://files.example-share.net/sh/qx7kw2hd91lzmnp/AAFr3tYbQeLp8VwZnKcDs2Hu?dl=0
• Link to the printwell templates used to begin this process....the one with the lines was about people intersecting (collaborating).....the organic shapes one more of a fluid feel of people coming together - the overall shape being largely spherical could represent a "global" feel.....anyway that is how I was thinking about these

```html
<!DOCTYPE html>
<html lang="en">
<head>
<meta charset="utf-8">
<title>berulo — business card front</title>
<link rel="stylesheet" href="https://fonts.googleapis.com/css2?family=Courgette&display=swap">
<style>
  :root {
    --ink-charcoal: #2b2e33;
    --map-tone: #3a3e44;
    --amethyst: #e34298;
    --amethyst-soft: #e667a6;
    --swoosh-light: #e8e9ea;
    --page-bg: #ffffff;
  }
  * { margin: 0; padding: 0; box-sizing: border-box; }
  html, body {
    width: 1200px;
    height: 740px;
    overflow: hidden;
    background: var(--page-bg);
  }
  .card-front {
    position: relative;
    width: 1200px;
    height: 740px;
    overflow: hidden;
    background: var(--ink-charcoal);
  }
  .card-art {
    position: absolute;
    inset: 0;
    width: 1200px;
    height: 740px;
    display: block;
  }
  .map-zone { fill: url(#mapGlow); }
  .swoosh-light { fill: var(--swoosh-light); }
  .field-amethyst { fill: var(--amethyst); }
  .brand-name {
    font-family: "Courgette", cursive;
    font-size: 100px;
    fill: var(--amethyst-soft);
    letter-spacing: 1px;
  }
</style>
</head>
<body>
  <main class="card-front">
    <svg class="card-art" viewBox="0 0 1000 617" preserveAspectRatio="xMidYMid meet">
      <defs>
        <radialGradient id="mapGlow" cx="0.5" cy="0.5" r="0.5">
          <stop offset="0" stop-color="#3a3e44" stop-opacity="0.9"/>
          <stop offset="0.7" stop-color="#3a3e44" stop-opacity="0.5"/>
          <stop offset="1" stop-color="#3a3e44" stop-opacity="0"/>
        </radialGradient>
      </defs>

      <rect class="map-zone" x="260" y="70" width="640" height="400" role="img"
            aria-label="Faint world map in the background"/>

      <path class="swoosh-light swoosh-upper"
            d="M45,0 L140,0 C180,170 250,290 342,360 C230,290 110,160 45,0 Z"/>

      <path class="swoosh-light swoosh-lower"
            d="M138,221 C280,390 620,520 1000,592 L1000,617 L0,617 Z"/>

      <path class="field-amethyst"
            d="M0,0 L38,0 C120,260 300,470 548,617 L0,617 Z"/>

      <text class="brand-name" x="543" y="305" text-anchor="middle">berulo</text>
    </svg>
  </main>
</body>
</html>
```